Kestrel Home Business Card Design

We need a business card for a Building company based in Queensland, Australia. Our colours are orange black and we do base all our homes design names and other aspect of our business on astrology. We want the consumer to perceive the company as professional and to attract investors to our company.We have over 20 years in the building industry.We pride ourselves on our innovation of designs and making the building process for anyone from families to investor a smooth and simple experience.
Business
Amelia Prichard0411752116PO Box 454, Mudgeerbaameliaprichard@zodiachomes.com

```html
<!DOCTYPE html>
<html lang="en">
<head>
<meta charset="utf-8">
<title>Kestrel Homes – Business Card</title>
<link rel="stylesheet" href="https://fonts.googleapis.com/css2?family=Open+Sans:wght@400;600;700&display=swap">
<style>
  :root {
    --backdrop: #9a9a98;
    --card-black: #050505;
    --info-band: #141414;
    --brand-orange: #f7931e;
    --paper-white: #f4f4f2;
    --text-white: #ffffff;
    --text-soft: #e6e6e6;
  }
  * { box-sizing: border-box; margin: 0; padding: 0; }
  html, body {
    width: 1200px; height: 900px; overflow: hidden;
    background: var(--backdrop);
    font-family: "Open Sans", Arial, sans-serif;
  }
  .stage {
    position: relative; width: 1200px; height: 900px;
    display: flex; flex-direction: column; align-items: center; justify-content: center; gap: 56px;
  }
  .card {
    position: relative; width: 560px; height: 320px;
    background: var(--card-black); overflow: hidden;
    box-shadow: 0 6px 18px rgba(0,0,0,0.25);
  }
  .card__stripe {
    position: absolute; left: 0; right: 0; bottom: 10px; height: 46px;
    background: var(--brand-orange);
    border-top: 8px solid var(--paper-white);
  }
  .card__edge {
    position: absolute; left: 0; right: 0; bottom: 0; height: 10px;
    background: var(--paper-white);
  }

  /* Back of card */
  .back__mark {
    position: absolute; left: 0; right: 0; top: 128px; transform: translateY(-50%);
    display: flex; align-items: center; justify-content: center; gap: 14px;
    white-space: nowrap;
  }
  .brand-dot {
    width: 30px; height: 30px; border-radius: 50%; flex: none;
    background: var(--brand-orange);
  }
  .back__name {
    color: var(--text-white); font-weight: 700; font-size: 34px; letter-spacing: 0.5px;
  }

  /* Front of card */
  .front__info-band {
    position: absolute; left: 0; right: 0; top: 172px; bottom: 64px;
    background: var(--info-band);
  }
  .front__brand {
    position: absolute; left: 34px; top: 64px;
    display: flex; align-items: center; gap: 10px; white-space: nowrap;
  }
  .front__brand .brand-dot { width: 22px; height: 22px; }
  .front__company {
    color: var(--text-white); font-weight: 700; font-size: 30px; letter-spacing: 0.3px;
  }
  .front__person {
    position: absolute; right: 34px; top: 70px; text-align: right; white-space: nowrap;
  }
  .person__name {
    color: var(--brand-orange); font-weight: 600; font-size: 17px; letter-spacing: 0.6px;
    text-transform: uppercase;
  }
  .person__title {
    color: var(--text-white); font-size: 13px; margin-top: 2px;
  }
  .contact {
    position: absolute;
    color: var(--text-soft); font-size: 11.5px; line-height: 21px;
  }
  .contact--address { left: 28px; top: 186px; }
  .contact--phone { left: 194px; top: 200px; }
  .contact--online { right: 22px; top: 200px; }
  .contact__row { display: flex; align-items: center; gap: 7px; white-space: nowrap; }
  .contact__row--indent { padding-left: 17px; }
  .icon { width: 10px; height: 10px; flex: none; fill: var(--brand-orange); }
</style>
</head>
<body>
<main class="stage">

  <section class="card card--back" aria-label="Business card, back">
    <div class="back__mark">
      <span class="brand-dot"></span>
      <span class="back__name">Kestrel Homes</span>
    </div>
    <div class="card__stripe"></div>
    <div class="card__edge"></div>
  </section>

  <section class="card card--front" aria-label="Business card, front">
    <div class="front__info-band"></div>

    <div class="front__brand">
      <span class="brand-dot"></span>
      <span class="front__company">Kestrel Homes</span>
    </div>

    <div class="front__person">
      <p class="person__name">Harriet Colvane</p>
      <p class="person__title">Managing Director</p>
    </div>

    <div class="contact contact--address">
      <p class="contact__row">
        <svg class="icon" viewBox="0 0 10 10"><path d="M5 0a3.5 3.5 0 0 0-3.5 3.5C1.5 6 5 10 5 10s3.5-4 3.5-6.5A3.5 3.5 0 0 0 5 0zm0 5a1.4 1.4 0 1 1 0-2.8A1.4 1.4 0 0 1 5 5z"/></svg>
        PO Box 872,
      </p>
      <p class="contact__row contact__row--indent">Queensland, Australia</p>
    </div>

    <div class="contact contact--phone">
      <p class="contact__row">
        <svg class="icon" viewBox="0 0 10 10"><path d="M1 3.5C1 2 2.5 1 5 1s4 1 4 2.5V4.5H7V3.4C6.5 3 5.8 2.9 5 2.9S3.5 3 3 3.4V4.5H1z"/><rect x="2" y="5.2" width="6" height="3.8" rx="0.6"/></svg>
        0487 309 625
      </p>
      <p class="contact__row">
        <svg class="icon" viewBox="0 0 10 10"><rect x="2.5" y="0" width="5" height="10" rx="1"/></svg>
        0487 309 625
      </p>
    </div>

    <div class="contact contact--online">
      <p class="contact__row">
        <svg class="icon" viewBox="0 0 10 10"><path d="M0 2h10v6H0z M0 2l5 3.5L10 2" stroke="#141414" stroke-width="0.8"/></svg>
        harrietcolvane@kestrelhomes.example
      </p>
      <p class="contact__row">
        <svg class="icon" viewBox="0 0 10 10"><path d="M4.2 5.8 L5.8 4.2" stroke="#f7931e" stroke-width="1.3"/><path d="M3.5 4 1.8 5.7a1.6 1.6 0 0 0 2.5 2.5L6 6.5M6.5 6l1.7-1.7a1.6 1.6 0 0 0-2.5-2.5L4 3.5" fill="none" stroke="#f7931e" stroke-width="1.3"/></svg>
        www.kestrelhomes.example
      </p>
    </div>

    <div class="card__stripe"></div>
    <div class="card__edge"></div>
  </section>

</main>
</body>
</html>
```